Tidy4all

Full service cleaning company. Specializing in commercial and apartment cleans.
Fully licensed and insured
Digital photos and invoices provided
for every job
For web designer...basic info as expected by a highend cleaning company that provides excellent service at reasonable pricing. We are going after large property management companies as well as not pricing ourselves out to help the local mom and pop companies as well.
Updates

Project Deadline Extended Reason: Everyone seems to be having trouble understanding that we are a dumpster company that is adding a cleaning side to the company. We want our clients to see Tidy4All as a separate branch of our our already established waste management company.We are not a regular cleaning company. We specialize in going after large commercial cleans and apartment cleans. I have now included info regarding a proposal for work and our invoice/job completion to make it clearer what we do Added Monday, July 20, 2015

Target Market(s)

Property Management companies in Savannah, Richmond Hill, Rincon, Hinesville and Midway Georgia

Industry/Entity Type

Cleaning Service

Coding

Coded - Design and coding required

Number of Pages Required

3 page

Requirements
Must have
• Nice home page with lots of photos (stock are fine) to convey exactly what we do (getting logo bid on right now on this sight).
• Information page with employee photos (can leave blank) need room for 4 photos and bios.
• Page or link to a static page for the dumpster company BinRun (logo for this is red and black file attached along with photo of dumpster. This page just needs to be one page with contact info and information about commercial dumpster.
• Basically this site is just a fluff page used for marketing purposes. Its content can be general and once created wont change much. Services and photos can be provided upon request but general layout and info is what we are looking for.

```html
<!DOCTYPE html>
<html lang="en">
<head>
<meta charset="utf-8">
<title>Tidy4All – Full Service Cleaning</title>
<link href="https://fonts.googleapis.com/css2?family=Noto+Serif:wght@400;700&family=Open+Sans:wght@400;600;700&display=swap" rel="stylesheet">
<style>
:root{
  --red:#e0262a;
  --red-dark:#b81c20;
  --ink:#222;
  --text:#666;
  --muted:#999;
  --page:#ffffff;
  --band:#ececec;
  --line:#dcdcdc;
  --green:#8cc21f;
  --green-dark:#6f9c12;
  --footer:#1d1d1d;
  --footer-bar:#121212;
}
*{box-sizing:border-box;margin:0;padding:0}
html,body{width:681px;height:1200px;overflow:hidden}
body{font-family:"Open Sans",Arial,sans-serif;color:var(--text);background:var(--page);font-size:8px;line-height:1.45}
.site{width:681px;height:1200px;position:relative}
.serif{font-family:"Noto Serif",Georgia,serif}

/* header */
.site-header{height:86px;position:relative;border-top:4px solid var(--ink)}
.brand{position:absolute;left:30px;top:22px;display:flex;align-items:center;gap:8px}
.brand-mark{width:26px;height:26px;background:var(--red)}
.brand-name{font-family:"Open Sans",Arial,sans-serif;font-weight:700;font-size:24px;color:var(--ink);letter-spacing:-.3px}
.contact-top{position:absolute;right:22px;top:6px;display:flex;align-items:center;gap:12px;font-size:9px;color:var(--ink)}
.contact-top .item{display:flex;align-items:center;gap:4px}
.phone-pill{background:var(--red);color:#fff;border-radius:12px;padding:3px 10px 3px 4px;font-size:13px;font-weight:700;display:flex;align-items:center;gap:6px}
.phone-pill .dot{width:16px;height:16px;border-radius:50%;background:#fff;display:flex;align-items:center;justify-content:center}
.main-nav{position:absolute;right:22px;top:56px;display:flex;gap:4px}
.main-nav a{display:block;background:var(--red);color:#fff;text-decoration:none;font-size:9px;font-weight:600;padding:6px 11px;border-radius:3px 3px 0 0}
.main-nav a.current{background:var(--ink)}

/* hero */
.hero{position:absolute;top:86px;left:0;width:681px;height:240px;background:linear-gradient(160deg,#6f8a5a 0%,#3f5a35 45%,#2c3d2a 70%,#596f4a 100%)}
.hero-caption{position:absolute;left:48px;top:140px;width:270px;background:rgba(20,20,20,.72);padding:9px 12px;color:#fff}
.hero-caption h1{font-size:14px;font-weight:700;line-height:1.2;margin-bottom:6px}
.hero-caption p{font-size:13px;font-weight:700;line-height:1.25}
.hero-dots{position:absolute;right:60px;bottom:12px;display:flex;gap:5px}
.hero-dots span{width:7px;height:7px;border-radius:50%;background:rgba(255,255,255,.6)}
.hero-dots span.on{background:var(--red)}

/* audience cards */
.audience{position:absolute;top:326px;left:0;width:681px;height:230px;background:var(--band);padding:18px 30px 0}
.cards{display:flex;gap:28px}
.card{flex:1;background:#fff;border-top:3px solid var(--red);padding:8px 9px 9px;box-shadow:0 2px 3px rgba(0,0,0,.08);height:190px;position:relative}
.card h2{font-family:"Noto Serif",Georgia,serif;font-size:13px;color:var(--ink);margin-bottom:6px}
.card .photo{height:66px;margin-bottom:8px}
.card p{font-size:7.5px;color:var(--muted)}
.read-more{position:absolute;right:9px;bottom:8px;font-size:7px;font-weight:700;color:var(--red);text-decoration:none}

/* welcome + schedule */
.intro{position:absolute;top:574px;left:30px;width:621px;height:178px;display:flex;gap:26px}
.welcome{flex:1.55;position:relative}
.section-title{font-family:"Noto Serif",Georgia,serif;font-size:14px;color:var(--ink);font-weight:700;padding-bottom:6px;border-bottom:1px solid var(--line);margin-bottom:8px}
.welcome p{font-size:7.5px;color:var(--muted);margin-bottom:8px}
.welcome .read-more{right:0;bottom:6px}
.schedule{flex:1}
.schedule form{display:flex;flex-direction:column;gap:5px}
.field{height:15px;border:1px solid var(--line);font-size:7px;color:var(--muted);padding:2px 5px;background:#fff}
.row{display:flex;gap:5px}
.row .field{flex:1}
.field.area{height:26px}
.submit{align-self:flex-end;background:var(--red);color:#fff;font-size:7px;font-weight:700;padding:4px 10px;border:none}

/* features */
.features{position:absolute;top:770px;left:30px;width:621px;height:190px;display:flex;gap:22px}
.feature{flex:1}
.feature h3{font-family:"Noto Serif",Georgia,serif;font-size:13px;color:var(--ink);margin-bottom:8px}
.feature .photo{height:70px;margin-bottom:8px}
.feature p{font-size:7.5px;color:var(--muted)}
.reasons{list-style:none}
.reasons li{font-size:7.5px;color:var(--muted);padding:4px 0 4px 14px;position:relative;border-bottom:1px solid #f0f0f0}
.reasons li svg{position:absolute;left:0;top:6px}

/* cta band */
.cta{position:absolute;top:968px;left:30px;width:621px;height:60px;background:var(--green);display:flex;align-items:center;justify-content:center;gap:12px;color:#fff}
.cta h2{font-family:"Noto Serif",Georgia,serif;font-size:13px;font-weight:700}
.cta .zip{width:92px;height:18px;background:#fff;font-size:7px;color:var(--muted);padding:3px 5px}
.cta .btn{background:#222;color:#fff;font-size:7px;font-weight:700;padding:5px 9px}

/* footer */
.site-footer{position:absolute;top:1044px;left:0;width:681px;height:142px;background:var(--footer);padding:14px 30px;display:flex;gap:24px;color:#bbb}
.site-footer h4{font-size:9px;color:#fff;font-weight:600;padding-bottom:5px;border-bottom:1px solid #3a3a3a;margin-bottom:6px}
.site-footer ul{list-style:none}
.site-footer li{font-size:7px;padding:1px 0}
.quick{width:110px}
.quick li::before{content:"› ";color:var(--red)}
.contact{width:170px}
.contact li{display:flex;gap:5px;align-items:flex-start;padding:2px 0}
.faq{width:150px}
.faq li::before{content:"• ";color:var(--red)}
.faq .more{color:#fff;font-weight:600}
.footer-brand{flex:1;display:flex;align-items:center;justify-content:center;gap:6px}
.footer-brand .mark{width:20px;height:20px;background:#555}
.footer-brand span{font-size:19px;font-weight:700;color:#666}
.copyright{position:absolute;top:1186px;left:0;width:681px;height:14px;background:var(--footer-bar);color:#888;font-size:6.5px;padding:2px 30px}
</style>
</head>
<body>
<div class="site">

  <header class="site-header">
    <div class="brand">
      <span class="brand-mark"></span>
      <span class="brand-name">Tidy4All</span>
    </div>
    <div class="contact-top">
      <span class="item">
        <svg width="10" height="8" viewBox="0 0 10 8"><rect x=".5" y=".5" width="9" height="7" fill="var(--red)"/><path d="M.5 .5 5 4.5 9.5 .5" stroke="#fff" fill="none"/></svg>
        info@tidy4all.com
      </span>
      <span class="phone-pill">
        <span class="dot"><svg width="9" height="9" viewBox="0 0 10 10"><path d="M2 1l2 2-1 1.5c.6 1.2 1.3 1.9 2.5 2.5L7 6l2 2-1.5 1.5C4 9 1 6 .5 2.5z" fill="var(--red)"/></svg></span>
        123-456-7890
      </span>
    </div>
    <nav class="main-nav">
      <a class="current" href="#">Home</a>
      <a href="#">About Us</a>
      <a href="#">Services</a>
      <a href="#">Think Green</a>
      <a href="#">Customer Review</a>
      <a href="#">Contact Us</a>
    </nav>
  </header>

  <section class="hero" role="img" aria-label="Green waste collection truck emptying a blue bin on a leafy street">
    <div class="hero-caption">
      <h1>We Are A Full Service Cleaning Company</h1>
      <p>Specializing in commercial and apartment cleans</p>
    </div>
    <div class="hero-dots"><span class="on"></span><span></span><span></span><span></span></div>
  </section>

  <section class="audience">
    <div class="cards">
      <article class="card">
        <h2>Home Owner</h2>
        <div class="photo" role="img" aria-label="Pile of household junk ready for removal" style="background:linear-gradient(135deg,#8a7454,#5b4a36)"></div>
        <p>We haul away clutter, old furniture and yard waste so your home stays tidy. Fast pickup, fair pricing and friendly crews on every visit.</p>
        <a class="read-more" href="#">READ MORE &gt;</a>
      </article>
      <article class="card">
        <h2>Business Owner</h2>
        <div class="photo" role="img" aria-label="Orange roll-off dumpster at a business site" style="background:linear-gradient(135deg,#c9773a,#8c4f27)"></div>
        <p>Scheduled service for offices, shops and rentals. Licensed, insured teams keep your property clean with photos and invoices for every job.</p>
        <a class="read-more" href="#">READ MORE &gt;</a>
      </article>
      <article class="card">
        <h2>Rent-a-Dumpster</h2>
        <div class="photo" role="img" aria-label="Row of rental dumpsters in a yard" style="background:linear-gradient(135deg,#b9c2c8,#6d7a84)"></div>
        <p>Choose the size you need and we drop it off. Load at your own pace, then call us and we take it away the same week.</p>
        <a class="read-more" href="#">READ MORE &gt;</a>
      </article>
    </div>
  </section>

  <section class="intro">
    <div class="welcome">
      <h2 class="section-title">Welcome To Tidy4All</h2>
      <p>Tidy4All is the cleaning branch of an established waste management company. We focus on large commercial cleans and apartment turnovers for property managers across the coastal region, bringing the same trusted crews and equipment to every site we serve.</p>
      <p>Every job includes a clear proposal up front, digital photos of the finished work and a detailed invoice. Large management firms and local family businesses alike get careful service at reasonable pricing, on a schedule that fits their tenants.</p>
      <a class="read-more" href="#">READ MORE &gt;</a>
    </div>
    <div class="schedule">
      <h2 class="section-title">Schedule A Service</h2>
      <form>
        <div class="field">Name</div>
        <div class="field">Phone</div>
        <div class="row"><div class="field">Date</div><div class="field">Time</div></div>
        <div class="field">Email</div>
        <div class="field area">Message</div>
        <span class="submit">SEND</span>
      </form>
    </div>
  </section>

  <section class="features">
    <div class="feature">
      <h3>24/7 Access</h3>
      <div class="photo" role="img" aria-label="Sign reading 24 hour service" style="background:linear-gradient(135deg,#9aa3aa,#4d565d)"></div>
      <p>Call any time of day or night. Our dispatch team answers around the clock and books your pickup or cleaning crew fast.</p>
    </div>
    <div class="feature">
      <h3>Reliable. Clean. Safe.</h3>
      <div class="photo" role="img" aria-label="Row of green commercial dumpsters" style="background:linear-gradient(135deg,#5fa04a,#2f6a2a)"></div>
      <p>Trained, licensed staff follow strict safety steps on every site and leave each unit spotless and ready for new tenants.</p>
    </div>
    <div class="feature">
      <h3>Why Chose Us</h3>
      <ul class="reasons">
        <li><svg width="8" height="8" viewBox="0 0 8 8"><path d="M1 4l2 2 4-4" stroke="var(--red)" stroke-width="1.5" fill="none"/></svg>Wide selection of container sizes</li>
        <li><svg width="8" height="8" viewBox="0 0 8 8"><path d="M1 4l2 2 4-4" stroke="var(--red)" stroke-width="1.5" fill="none"/></svg>Flexible, timely pickup and delivery</li>
        <li><svg width="8" height="8" viewBox="0 0 8 8"><path d="M1 4l2 2 4-4" stroke="var(--red)" stroke-width="1.5" fill="none"/></svg>Fair and clear pricing</li>
        <li><svg width="8" height="8" viewBox="0 0 8 8"><path d="M1 4l2 2 4-4" stroke="var(--red)" stroke-width="1.5" fill="none"/></svg>Easy online ordering and booking</li>
        <li><svg width="8" height="8" viewBox="0 0 8 8"><path d="M1 4l2 2 4-4" stroke="var(--red)" stroke-width="1.5" fill="none"/></svg>Online account management</li>
        <li><svg width="8" height="8" viewBox="0 0 8 8"><path d="M1 4l2 2 4-4" stroke="var(--red)" stroke-width="1.5" fill="none"/></svg>Instant online pricing</li>
      </ul>
    </div>
  </section>

  <section class="cta">
    <h2>Ready to get started? See what dumpsters are available in your area.</h2>
    <span class="zip">Enter ZIP Code</span>
    <span class="btn">SHOW PRODUCTS</span>
  </section>

  <footer class="site-footer">
    <div class="quick">
      <h4>Quick Links</h4>
      <ul>
        <li>Home</li><li>About Us</li><li>Services</li><li>Think Green</li><li>Customer Review</li><li>Contact Us</li>
      </ul>
    </div>
    <div class="contact">
      <h4>Contact Information</h4>
      <ul>
        <li><svg width="7" height="9" viewBox="0 0 7 9"><path d="M3.5 9S0 5 0 3.5a3.5 3.5 0 0 1 7 0C7 5 3.5 9 3.5 9z" fill="var(--red)"/></svg>120 Harbor Street, Suite 4, Coastal City, GA 31400</li>
        <li><svg width="8" height="8" viewBox="0 0 10 10"><path d="M2 1l2 2-1 1.5c.6 1.2 1.3 1.9 2.5 2.5L7 6l2 2-1.5 1.5C4 9 1 6 .5 2.5z" fill="var(--red)"/></svg>123-456-7890</li>
        <li><svg width="8" height="7" viewBox="0 0 10 8"><rect x=".5" y=".5" width="9" height="7" fill="var(--red)"/></svg>info@tidy4all.com</li>
      </ul>
    </div>
    <div class="faq">
      <h4>FAQ's</h4>
      <ul>
        <li>What sizes of dumpsters do you rent?</li>
        <li>How much does a cleanup cost?</li>
        <li>How much does delivery cost?</li>
        <li>What items are not allowed?</li>
        <li>How long can we keep it?</li>
        <li class="more">View FAQs</li>
      </ul>
    </div>
    <div class="footer-brand">
      <span class="mark"></span><span>Tidy4All</span>
    </div>
  </footer>
  <div class="copyright">© 2015 Tidy4All | All rights reserved</div>

</div>
</body>
</html>
```